wealth management firm, professional group, new model

we have a logo that works but we need a card, white background using our colors...clean look

our tag line if can be used in

Steady Plans for Lasting Wealth

```html
<!DOCTYPE html>
<html lang="en">
<head>
<meta charset="utf-8">
<title>Arcova Wealth Partners – Business Card</title>
<link href="https://fonts.googleapis.com/css2?family=Montserrat:wght@400;500&display=swap" rel="stylesheet">
<style>
  :root {
    --backdrop: #232323;
    --card: #ececec;
    --navy: #1f3152;
    --ink: #14233f;
    --white: #ffffff;
  }
  * { margin: 0; padding: 0; box-sizing: border-box; }
  html, body {
    width: 1200px; height: 576px; overflow: hidden;
    background: var(--backdrop);
    font-family: "Montserrat", sans-serif;
    color: var(--ink);
  }
  .stage { position: relative; width: 1200px; height: 576px; }
  .card {
    position: absolute;
    background: var(--card);
    border-radius: 9px;
    overflow: hidden;
  }
  .card--front { left: 102px; top: 139px; width: 484px; height: 292px; }
  .card--back  { left: 596px; top: 138px; width: 480px; height: 291px; }

  .wordmark { position: absolute; text-align: center; font-weight: 400; white-space: nowrap; }
  .wordmark__name { display: block; letter-spacing: 0.38em; }
  .wordmark__sub { display: block; letter-spacing: 0.12em; }

  .card--front .wordmark { left: 0; width: 100%; top: 133px; }
  .card--front .wordmark__name { font-size: 40px; line-height: 1; padding-left: 0.38em; }
  .card--front .wordmark__sub { font-size: 14px; margin-top: 18px; }

  .wave { position: absolute; left: 0; top: 0; width: 480px; height: 130px; }

  .tagline {
    position: absolute; right: 34px; top: 19px;
    text-align: right; color: var(--white);
    font-size: 13px; line-height: 18px; letter-spacing: 0.05em;
  }

  .card--back .wordmark { left: 28px; top: 125px; width: 196px; }
  .card--back .wordmark__name { font-size: 31px; line-height: 1; letter-spacing: 0.33em; padding-left: 0.33em; }
  .card--back .wordmark__sub { font-size: 12.5px; margin-top: 14px; }

  .person { position: absolute; left: 30px; top: 218px; }
  .person__name { font-size: 22px; font-weight: 500; line-height: 1.1; }
  .person__role { font-size: 13px; margin-top: 3px; }

  .contacts { position: absolute; right: 34px; top: 201px; list-style: none; }
  .contacts li {
    display: flex; justify-content: flex-end; align-items: center;
    font-size: 12.5px; height: 20px;
  }
  .contacts svg { width: 10px; height: 10px; margin-left: 8px; fill: var(--ink); }
</style>
</head>
<body>
<main class="stage">
  <section class="card card--front">
    <div class="wordmark">
      <span class="wordmark__name">ARCOVA</span>
      <span class="wordmark__sub">WEALTH PARTNERS</span>
    </div>
  </section>

  <section class="card card--back">
    <svg class="wave" viewBox="0 0 480 130" aria-hidden="true">
      <path fill="var(--navy)" d="M0,0 H480 V90 C425,98 385,82 335,56 C265,22 150,4 0,30 Z"/>
      <path fill="var(--navy)" d="M40,58 C150,22 262,36 332,72 C392,102 432,106 480,99 V114 C420,122 372,108 322,86 C244,52 150,38 40,58 Z"/>
    </svg>
    <p class="tagline">Steady Plans for<br>Lasting Wealth</p>

    <div class="wordmark">
      <span class="wordmark__name">ARCOVA</span>
      <span class="wordmark__sub">WEALTH PARTNERS</span>
    </div>

    <div class="person">
      <p class="person__name">Mark Ellison</p>
      <p class="person__role">Managing Director</p>
    </div>

    <ul class="contacts">
      <li>555-014-2290
        <svg viewBox="0 0 10 10"><path d="M1,4 C1,1.5 9,1.5 9,4 L7.5,4.5 L7,3.5 H3 L2.5,4.5 Z M2.5,5 H7.5 L8.5,9 H1.5 Z"/></svg>
      </li>
      <li>mark@arcovawealth.com
        <svg viewBox="0 0 10 10"><path d="M0,2 H10 V8.5 H0 Z M0.8,2.6 L5,5.8 L9.2,2.6 V2.8 L5,6.2 L0.8,2.8 Z" fill-rule="evenodd"/></svg>
      </li>
      <li>www.arcovawealth.com
        <svg viewBox="0 0 10 10"><circle cx="5" cy="5" r="4.3" fill="none" stroke="var(--ink)" stroke-width="1"/><ellipse cx="5" cy="5" rx="1.8" ry="4.3" fill="none" stroke="var(--ink)" stroke-width="0.8"/><path d="M0.7,5 H9.3" stroke="var(--ink)" stroke-width="0.8"/></svg>
      </li>
    </ul>
  </section>
</main>
</body>
</html>
```